Web Design job - Condo Debts Collection Business needs a Web Design

I need a site for a client, who works with condo debts collection, and ensure all revenues provided by condo fees will be always available to the building manager of condo on a specific date, regardless of defaults.
I have the visual identity (logo, slogan and colors) of the company, and some requirements on layout (kind of slider, menu options, phone number on a noble position, etc) - maybe I can do a sketch, but I like the idea of give some freedom to designer.

*** PLEASE, we have no interest in templates. We want something new***

Target Market(s)

I have two targets for this design: - Condominium's building manager. This target is looking for a solution to overdue debts on it's condo. - Residents on condominiums. This target wants to live in a better place, where their neighbors pay their condominium fees on time.

Number of Pages Required

1 page

Requirements
Must have
• - Slider with title, some short text related, a nice image (I prefer happy and/or peaceful family, people doing business, happy friends, and so on).
• - I have a special attention to menu. I'm looking for one I can have a nice effect, more elegant, charming, kind of innovative.
• - Phone number on the top (or clearly visible).
• - Member log in area or icon on the top (or clearly visible).
• - News/articles area.
• - Modern fonts, with good quality, sans-serif on areas where reading is more intensive (prefer Google web-fonts).
• - Colors specified on attached files.
Nice to have
• - Clear background color, cause it's better to read larger texts (like articles). Dark backgrounds makes reading difficult.
• - A site with effects (like shadows, lines, curves, gradients, lights) is usually pretty.
• - I pay attention on beautiful footers.
Should not have
• - Images with a lot of money (I don't sell richness, I sell tranquility, peace, harmony, safety).
• - Poor menu.

```html
<!DOCTYPE html>
<html lang="en">
<head>
<meta charset="utf-8">
<title>Condara — Condominium Fee Collection</title>
<link rel="stylesheet" href="https://fonts.googleapis.com/css2?family=Poppins:ital,wght@0,400;0,500;0,600;0,700;1,400&display=swap">
<style>
  :root {
    --orange: #f0a414;
    --orange-deep: #e8960a;
    --ink: #1d1d1d;
    --text: #3a3a3a;
    --muted: #666;
    --light: #f1f1f1;
    --grey-band: #e9e9ea;
    --footer: #1b1b1b;
    --white: #ffffff;
  }
  * { box-sizing: border-box; margin: 0; padding: 0; }
  html, body { width: 1200px; height: 3125px; overflow: hidden; }
  body { font-family: "Poppins", sans-serif; color: var(--text); background: var(--white); position: relative; }
  .abs { position: absolute; }

  /* Header */
  .site-header { position: absolute; left: 0; top: 0; width: 1200px; height: 142px; background: var(--light); }
  .topbar { position: absolute; left: 522px; top: 0; right: 0; height: 70px; background: var(--orange); border-bottom-left-radius: 40px; color: var(--white); font-size: 15px; }
  .topbar .phone { position: absolute; left: 78px; top: 24px; }
  .topbar .login { position: absolute; left: 422px; top: 24px; }
  .brand { position: absolute; left: 100px; top: 30px; display: flex; align-items: center; gap: 16px; }
  .brand .mark { width: 64px; height: 64px; background: var(--orange); }
  .brand .name { font-size: 54px; font-weight: 700; color: var(--ink); letter-spacing: -1px; line-height: 1; }
  .main-nav { position: absolute; left: 528px; top: 92px; display: flex; gap: 24px; font-size: 15px; color: var(--ink); }
  .main-nav .active { color: var(--orange); }
  .search-icon { position: absolute; left: 1078px; top: 96px; }

  /* Hero */
  .hero { position: absolute; left: 0; top: 142px; width: 1200px; height: 690px; overflow: hidden; }
  .hero-photo { position: absolute; inset: 0; background: linear-gradient(110deg, #b8882a 0%, #e6b64a 35%, #f6d684 55%, #d39a2e 80%, #a8701c 100%); }
  .hero-wave { position: absolute; left: 0; bottom: 0; }
  .hero-copy { position: absolute; right: 100px; top: 210px; text-align: right; color: var(--ink); }
  .hero-copy h1 { font-size: 43px; font-weight: 600; line-height: 1.2; }
  .hero-copy p { font-size: 17px; line-height: 1.55; margin-top: 14px; }
  .btn-outline { display: inline-block; margin-top: 24px; padding: 13px 34px; border: 2px solid var(--white); border-radius: 30px; color: var(--white); font-size: 16px; font-weight: 600; }
  .slider-arrow { position: absolute; top: 282px; }

  /* Who we are */
  .who { position: absolute; left: 0; top: 880px; width: 1200px; height: 400px; }
  .section-title { font-size: 33px; font-weight: 600; color: var(--ink); }
  .who .section-title { position: absolute; left: 100px; top: 34px; }
  .who .lead { position: absolute; left: 100px; top: 100px; width: 440px; font-size: 13.5px; font-style: italic; line-height: 1.8; color: var(--ink); }
  .who .body { position: absolute; left: 100px; top: 153px; width: 450px; font-size: 13.5px; line-height: 1.8; color: var(--ink); }
  .btn-solid { display: inline-block; padding: 10px 26px; background: var(--orange); color: var(--white); border-radius: 20px; font-size: 12px; font-weight: 500; }
  .who .btn-solid { position: absolute; left: 100px; top: 295px; }
  .who-frame { position: absolute; left: 655px; top: 22px; width: 440px; height: 322px; background: var(--orange); }
  .who-photo { position: absolute; left: 626px; top: 40px; width: 440px; height: 285px; background: linear-gradient(180deg, #f4f4f4 0%, #cfd3d6 55%, #8d959b 100%); box-shadow: 0 8px 20px rgba(0,0,0,.15); }

  /* Mission / Vision */
  .mission { position: absolute; left: 0; top: 1305px; width: 1200px; height: 420px; }
  .mission-photo { position: absolute; left: 0; top: 0; width: 690px; height: 420px; background: linear-gradient(90deg, #6f7a8c 0%, #aab0b8 50%, #dcdde0 100%); clip-path: polygon(0 0, 100% 0, 490px 100%, 0 100%); }
  .mission-panel { position: absolute; left: 490px; top: 25px; width: 710px; height: 380px; background: var(--white); clip-path: polygon(190px 0, 100% 0, 100% 100%, 0 100%); filter: drop-shadow(0 4px 12px rgba(0,0,0,.12)); }
  .mission h3 { font-size: 22px; font-weight: 600; color: var(--orange); }
  .mission p { font-size: 13.5px; line-height: 1.8; color: var(--ink); margin-top: 12px; }
  .mission .block-mission { position: absolute; left: 630px; top: 85px; width: 460px; }
  .mission .block-vision { position: absolute; left: 595px; top: 225px; width: 460px; }

  /* What we do */
  .services { position: absolute; left: 0; top: 1725px; width: 1200px; height: 635px; background: var(--grey-band); }
  .services .section-title { position: absolute; left: 102px; top: 118px; }
  .service { position: absolute; top: 200px; width: 308px; text-align: center; }
  .service .thumb { height: 210px; position: relative; display: flex; flex-direction: column; align-items: center; justify-content: center; color: var(--white); }
  .service .thumb h4 { font-size: 21px; font-weight: 600; text-shadow: 0 1px 3px rgba(0,0,0,.4); }
  .service .thumb .see-more { font-size: 14px; font-weight: 600; margin-top: 28px; }
  .service p { font-size: 13.5px; line-height: 1.8; color: var(--ink); margin-top: 18px; padding: 0 4px; }
  .thumb.debt { background: linear-gradient(160deg, #6d6d6d, #2f2f2f); }
  .thumb.invoice { background: linear-gradient(160deg, #f3b236, #e8950c); }
  .thumb.insolvency { background: linear-gradient(160deg, #9a9a9a, #3e3e3e); }

  /* News */
  .news { position: absolute; left: 0; top: 2360px; width: 1200px; height: 420px; }
  .news .section-title { position: absolute; left: 0; width: 1200px; text-align: center; top: 52px; font-size: 31px; }
  .news-item { position: absolute; top: 138px; display: flex; gap: 18px; }
  .news-item .thumb { width: 222px; height: 202px; border: 4px solid var(--white); box-shadow: 0 2px 8px rgba(0,0,0,.18); }
  .news-item .info { width: 260px; padding-top: 4px; }
  .news-item h5 { font-size: 16px; font-weight: 500; color: var(--orange); }
  .news-item .date { font-size: 13px; color: var(--ink); margin-top: 10px; }
  .news-item p { font-size: 13.5px; line-height: 1.95; color: var(--ink); margin-top: 12px; }
  .news-item .read-more { font-size: 15px; font-weight: 500; color: var(--orange); margin-top: 8px; display: block; }
  .pager { position: absolute; top: 382px; left: 452px; display: flex; align-items: center; gap: 20px; font-size: 14px; color: var(--muted); }
  .pager .dots { display: flex; gap: 5px; }
  .pager .dots i { width: 10px; height: 10px; border-radius: 50%; background: #999; display: block; }
  .pager .dots i.on { background: var(--orange); }
  .pager .next { color: var(--orange); }

  /* Footer */
  .site-footer { position: absolute; left: 0; top: 2760px; width: 1200px; height: 365px; color: var(--white); }
  .footer-contacts { position: absolute; top: 180px; left: 228px; display: flex; font-size: 14px; }
  .contact { display: flex; align-items: center; gap: 18px; }
  .contact .icon { width: 46px; height: 46px; border-radius: 50%; border: 1px solid #555; display: flex; align-items: center; justify-content: center; }
  .footer-nav { position: absolute; top: 262px; left: 0; width: 1200px; display: flex; justify-content: center; gap: 38px; font-size: 14px; }
  .footer-rule { position: absolute; top: 306px; left: 100px; width: 1000px; height: 1px; background: #444; }
  .copyright { position: absolute; top: 326px; left: 100px; font-size: 13px; }
  .socials { position: absolute; top: 318px; left: 993px; display: flex; gap: 10px; }
  .socials span { width: 34px; height: 34px; border-radius: 50%; border: 1.5px solid #bbb; display: block; }
</style>
</head>
<body>

<header class="site-header">
  <div class="brand"><span class="mark"></span><span class="name">Condara</span></div>
  <div class="topbar">
    <span class="phone">Call Us: +1 555 014 2290</span>
    <span class="login">Member Login</span>
  </div>
  <nav class="main-nav">
    <span class="active">Home</span><span>About Us</span><span>Why Choose Us</span><span>Services</span><span>Blog</span><span>Contact Us</span>
  </nav>
  <svg class="search-icon" width="16" height="16" viewBox="0 0 16 16" fill="none" stroke="#f0a414" stroke-width="2"><circle cx="6.5" cy="6.5" r="5"/><line x1="10.5" y1="10.5" x2="15" y2="15"/></svg>
</header>

<section class="hero">
  <div class="hero-photo" role="img" aria-label="Happy family playing outdoors in warm sunset light"></div>
  <svg class="hero-wave" width="1200" height="120" viewBox="0 0 1200 120" preserveAspectRatio="none">
    <path d="M0 105 C 250 45, 520 40, 760 75 C 950 100, 1080 60, 1200 55 L1200 120 L0 120 Z" fill="rgba(255,255,255,.45)"/>
    <path d="M0 120 C 260 60, 540 55, 780 90 C 960 115, 1090 80, 1200 70 L1200 120 Z" fill="#ffffff"/>
  </svg>
  <div class="hero-copy">
    <h1>Grow Your Business</h1>
    <p>Sed ut perspiciatis unde omnis iste natus<br>error sit voluptatem accusantium</p>
    <span class="btn-outline">READ MORE</span>
  </div>
  <svg class="slider-arrow" style="left:0" width="64" height="130" viewBox="0 0 64 130"><path d="M0 0 L64 65 L0 130 Z" fill="rgba(255,255,255,.85)"/><path d="M30 58 L23 65 L30 72" stroke="#f0a414" stroke-width="2.5" fill="none"/></svg>
  <svg class="slider-arrow" style="right:0" width="64" height="130" viewBox="0 0 64 130"><path d="M64 0 L0 65 L64 130 Z" fill="rgba(255,255,255,.85)"/><path d="M34 58 L41 65 L34 72" stroke="#f0a414" stroke-width="2.5" fill="none"/></svg>
</section>

<section class="who">
  <h2 class="section-title">Who We Are</h2>
  <p class="lead">Sed ut perspiciatis unde omnis iste natus error sit voluptatem accusantium doloremque laudantium</p>
  <p class="body">But I must explain to you how all this mistaken idea of denouncing pleasure and praising pain was born and I will give you a complete account of the system, and expound the actual teachings of the great explorer of the truth, the master-builder of human happiness.</p>
  <span class="btn-solid">READ MORE</span>
  <div class="who-frame"></div>
  <div class="who-photo" role="img" aria-label="Business team meeting around a glass conference table"></div>
</section>

<section class="mission">
  <div class="mission-photo" role="img" aria-label="Smiling businessman giving a thumbs up in a bright office"></div>
  <div class="mission-panel"></div>
  <div class="block-mission">
    <h3>Our Mission</h3>
    <p>But I must explain to you how all this mistaken idea of denouncing pleasure and praising pain was born and I will give you a complete account of the system, and expound.</p>
  </div>
  <div class="block-vision">
    <h3>Our Vision</h3>
    <p>But I must explain to you how all this mistaken idea of denouncing pleasure and praising pain was born and I will give you a complete account of the system, and expound.</p>
  </div>
</section>

<section class="services">
  <h2 class="section-title">What We Do</h2>
  <div class="service" style="left:104px">
    <div class="thumb debt" role="img" aria-label="Hand signing a debt collection document"><h4>Debt Collection</h4></div>
    <p>At vero eos et accusamus et iusto odio dignissimos ducimus qui blanditiis praesentium voluptatum deleniti atque corrupti quos dolores et quas molestias</p>
  </div>
  <div class="service" style="left:444px">
    <div class="thumb invoice" role="img" aria-label="Person reviewing invoices at a desk"><h4>Invoice Checking</h4><span class="see-more">See More</span></div>
    <p>At vero eos et accusamus et iusto odio dignissimos ducimus qui blanditiis praesentium voluptatum deleniti atque corrupti quos dolores et quas molestias</p>
  </div>
  <div class="service" style="left:783px">
    <div class="thumb insolvency" role="img" aria-label="Calculator and financial papers on a desk"><h4>Insolvency Services</h4></div>
    <p>At vero eos et accusamus et iusto odio dignissimos ducimus qui blanditiis praesentium voluptatum deleniti atque corrupti quos dolores et quas molestias</p>
  </div>
</section>

<section class="news">
  <h2 class="section-title">Latest News</h2>
  <article class="news-item" style="left:90px">
    <div class="thumb" role="img" aria-label="Group of smiling business people" style="background:linear-gradient(160deg,#e9e9e9,#6b6258)"></div>
    <div class="info">
      <h5>Nemo enim ipsam voluptatem</h5>
      <div class="date">22 June 2018</div>
      <p>Lorem ipsum dolor sit amet, consectetur adipiscing elit, sed do eiusmod tempor incididunt ut labore et dolore magna aliqua. Ut</p>
      <span class="read-more">Read More</span>
    </div>
  </article>
  <article class="news-item" style="left:620px">
    <div class="thumb" role="img" aria-label="Young professional working on a laptop" style="background:linear-gradient(160deg,#f3e2b8,#8a8278)"></div>
    <div class="info">
      <h5>Nemo enim ipsam voluptatem</h5>
      <div class="date">30 June 2018</div>
      <p>Lorem ipsum dolor sit amet, consectetur adipiscing elit, sed do eiusmod tempor incididunt ut labore et dolore magna aliqua. Ut</p>
      <span class="read-more">Read More</span>
    </div>
  </article>
  <div class="pager">
    <span>⟵ &nbsp;Previous</span>
    <span class="dots"><i class="on"></i><i></i><i></i></span>
    <span class="next">Next &nbsp;⟶</span>
  </div>
</section>

<footer class="site-footer">
  <svg class="abs" style="left:0;top:0" width="1200" height="365" viewBox="0 0 1200 365" preserveAspectRatio="none">
    <path d="M0 10 C 200 20, 380 100, 620 95 C 840 90, 1000 40, 1200 60 L1200 365 L0 365 Z" fill="#3a3a3a"/>
    <path d="M0 30 C 220 40, 400 125, 630 118 C 850 112, 1010 70, 1200 85 L1200 365 L0 365 Z" fill="#1b1b1b"/>
  </svg>
  <div class="footer-contacts">
    <div class="contact" style="width:330px">
      <span class="icon"><svg width="16" height="20" viewBox="0 0 16 20"><path d="M8 0a7 7 0 0 0-7 7c0 5 7 13 7 13s7-8 7-13a7 7 0 0 0-7-7z" fill="#fff"/><circle cx="8" cy="7" r="2.5" fill="#1b1b1b"/></svg></span>
      <span style="line-height:1.9">#24, 48 Harbor Lane, Springfield<br>FL 2040</span>
    </div>
    <div class="contact" style="width:210px">
      <span class="icon"><svg width="18" height="18" viewBox="0 0 24 24"><path d="M6.6 10.8a15 15 0 0 0 6.6 6.6l2.2-2.2a1 1 0 0 1 1-.25 11.4 11.4 0 0 0 3.6.57 1 1 0 0 1 1 1V20a1 1 0 0 1-1 1A17 17 0 0 1 3 4a1 1 0 0 1 1-1h3.5a1 1 0 0 1 1 1c0 1.25.2 2.45.57 3.6a1 1 0 0 1-.25 1z" fill="#fff"/></svg></span>
      <span>+1 555 014 2290</span>
    </div>
    <div class="contact">
      <span class="icon"><svg width="18" height="14" viewBox="0 0 18 14"><rect x="0" y="0" width="18" height="14" rx="1.5" fill="#fff"/><path d="M1 1 L9 8 L17 1" stroke="#1b1b1b" stroke-width="1.6" fill="none"/></svg></span>
      <span>info@condara.com</span>
    </div>
  </div>
  <nav class="footer-nav">
    <span>Home</span><span>About Us</span><span>Why Choose Us</span><span>Services</span><span>Blog</span><span>Contact Us</span>
  </nav>
  <div class="footer-rule"></div>
  <div class="copyright">© 2018 Condara | All Rights Reserved</div>
  <div class="socials"><span></span><span></span><span></span></div>
</footer>

</body>
</html>
```